Digital Imaging Website Design Project

This project is for 3 page designs - The main Home page design, department page design & content page design which will utilize most of the home page components.

Client Background - http://www.klmvxco.example

An almost Forty year old established printing company that has a large client base of architect/engineering, as the print shop opened up as a blueprinting company, and over the years has grown, changed and expanded to offer document and digital file management for this industry. KLMVxco. has also always offered color printing services, but recently has expanded their color department to be able to offer amazing dimensional printing, and extreme cutting technology.

These new products and services will be targeted to new industries for repeatable printing needs, promotional, point of purchase color printing, as well as in-store, interior decor/wall. These new printing services are only offered by KLMVXCO in their area, and they want to convey that they are on the leading edge of color printing technology, while at the same time, not eliminating their existing primary business scaring away their traditional client base of architectural/engineering firms that use them for large format printing, scanning and document management services.

1 - Home Page Design
Primary Goals of the design:

1.Provide a new, eye catching engaging website that conveys the above expansion/growth/cutting edge company.
2.Full screen design please to move away from the 'center' bordered up website they currently have.
3.Design Components – We don't have any media to provide you with exception of our logo. We're looking for fresh design that is exciting and engaging imagery. Additionally, we are working on a color/effected version of our logo to place on the color division page, and this will probably tie in with the design you create for us.
4.It should be designed to be able to work as a responsive design as well so that when installed, will work across devices etc..
5.Colors – Same color scheme, but if you have an accent color you'd like to use to make the site pop, go for it!

Requirements:
1.The 4 divisions of the company should be the main feature so that the client depending on which department they are needing, will see those 4 choices clearly in the design, and they'll know to click on one of them to get more information and to their needed services.

2.The main goal of the site is to get visitors to place an order, there should be a feature on the home page for this call to action.

3.Put in an element that communicates the main benefit of KLMVxco. - an area for a 1-line Statement/Call to Action / Overall Company Benefit/

4.The 4 divisions need to have eye catching elements related to their products and services, and that clearly illustrate that the user should click on that to go to the appropriate area for products and services

Reprographics
This department is specifically geared to architect/engineering industry
BYLine for optional Use: Partnering with Building Industry Providers since 1975
Related pages for better understanding:
http://www.klmvxco.example/services/portland_professional_printing_services
http://www.klmvxco.example/services/reprographics
Digital File Management
This department is related to Architect/engineers, but can also apply to any other industry needing electronic document management, scanning, or archival services.
BYLine for optional use: Effective & Efficient Digital Solutions at every level.
Related Pages:
http://www.klmvxco.example/colorgraphics/electronic_file_document_management
http://www.klmvxco.example/colorgraphics/document_scanning_service
http://www.klmvxco.example/services/scanning_and_archiving

Color Graphics
This Department is newly expanded / has expanded services / they are focusing more of their efforts on this department and is a key reason for updated website design.
This Department image/representation should be stellar in the imagery to convey the excellence of the color department the services availble.
One of their newest products/services is dimensional printing – not 3-D, but raised element printing. Essentially a client could pick components on their graphic that that they want to 'bump' out, and additional layers would be put in place to create a popped out, dimensional effect. * Bonus points for creating the color department image that effectively conveys this new service – whether it's showing an abstract image/element that is actually raised off the page/paper/component. Additionally the color dimensional printing can be done on practically any material – glass, vinyl, material etc.... Please let me know if you have any questions on this.
BYLine for optional Use: See How Our Color Stands Out From the Rest
Related pages:
http://www.klmvxco.example/colorgraphics
http://www.klmvxco.example/colorgraphics/color_digital_imaging

Equipment & Supplies
This department provides specific supplies and hardware vs. printing products/services. Our largest client base is architects/engineers, but is not limited to this industry. Typical equipment is large printers, and supplies are typically paper products geared to the large format printing services, for the architect/engineers industry.
Byline for optional Use: In-House Printing & Fulfillment Services
Related pages:
http://www.klmvxco.example/tarvo_ulix_equipment_sales
http://www.klmvxco.example/supplies

Additionally - Possibly have descriptive text sections below these 4 elements, but this is optional.

2.) Department/Division Page design -

This page should pull the home page element to over based on which division is selected.
Have a submenu design incorporated so that users can navigate to all the products and services that will be listed under that division
Contain a plugin design for FAQs – so that depending on which division page they are on, the appropriate FAQ's would display for use to have easy access to.
Contain a plugin design for – Contact Us easy form – short form –
Name
Company
Number
Email
Project Details/Questions: Text box

3.)Content Page design
This page should have main area for content
Area for an image with slideshow of other supporting images
Optional area for video – most (99%) of the pages will not have videos, but in the case we do, would like an area that will display videos effectively.
Optional FAQ plugin display
Contact plugin display

Global Elements:

Static and very visible site features that are in a position so that if user clicks beyond home page will still see these are:
Get a Quote
Place Order
Digital Plan-room
Call Today - 555-384-7290

Other global components:
SM Icons – QN, Chirpa, Workrung
Rotating Testimonial

Navigational Menu:
The KVX Difference
About
Sustainability
Products & Services
Reprograhics
Digital File Management
Color Graphics
Equipment & Supplies
Login
Blog
Contact Us

After the contest – What would be great to have is when a user clicks on one of the departments, it takes that visual element and continues onto it's department page for a smaller but related image - But this may be an after this web design contest.

Additionally will need some other design work on the interior pages, as well, so hoping to find a great designer to complete the other tasks – as well as be the go-to for future endeavors!

Thanks for looking at the project, and I look forward to any questions you may have.
Updates

Looking forward to hearing from interested designers! - If you're curious about my work, you can find my profile at:  https://www.jobrilly.example/users/~07f3b92e61cd5a0b48

Target Market(s)

Please see description

Industry/Entity Type

Electronic

Requirements
Must have
• Please see description

```html
<!DOCTYPE html>
<html lang="en">
<head>
<meta charset="utf-8">
<title>KVX Digital Imaging</title>
<link href="https://fonts.googleapis.com/css2?family=Titillium+Web:wght@300;400;600;700&display=swap" rel="stylesheet">
<style>
:root{
  --brand:#4b4ca0;
  --brand-dark:#3c3d86;
  --brand-light:#5b5cb0;
  --orange:#f7931e;
  --cyan:#2ab7d6;
  --red:#e63a45;
  --band:#e8eaed;
  --card:#efefef;
  --ink:#222;
  --muted:#9a9a9a;
  --rule:#e2e2e2;
}
*{margin:0;padding:0;box-sizing:border-box}
html,body{width:767px;height:1200px;overflow:hidden;background:#fff}
body{position:relative;font-family:'Titillium Web',sans-serif;color:var(--ink)}
.abs{position:absolute}
.header{left:0;top:0;width:767px;height:66px;background:var(--brand)}
.brand{left:115px;top:18px;display:flex;align-items:center;gap:8px;color:#fff}
.brand-mark{width:26px;height:26px;border-radius:50%;background:#fff}
.brand-name{font-weight:700;font-size:18px;line-height:1}
.brand-sub{font-size:6px;line-height:7px;font-weight:600;text-transform:uppercase;margin-top:2px}
.nav{left:313px;top:0;height:66px;display:flex}
.nav a{color:#fff;text-decoration:none;font-size:8px;line-height:8px;font-weight:600;padding:27px 4px 0 4px;height:66px}
.nav a.active{background:var(--brand-light);padding-left:5px;padding-right:5px}
.hero{left:0;top:66px;width:767px;height:241px;background:linear-gradient(100deg,#2a2a32 0%,#6b2b3c 30%,#c83a55 48%,#2f4a7e 70%,#1e2a4a 100%)}
.arrow{top:176px;width:21px;height:20px;background:var(--brand);display:flex;align-items:center;justify-content:center}
.hero-title{left:110px;top:194px;font-size:26px;font-weight:700;color:#fff;letter-spacing:-0.5px}
.hero-text{left:110px;top:232px;width:260px;font-size:8px;line-height:12px;color:#fff}
.btn-orange{left:111px;top:268px;width:74px;height:24px;background:var(--orange);color:#fff;font-size:9.5px;font-weight:600;display:flex;align-items:center;justify-content:center}
.quote-band{left:0;top:307px;width:767px;height:49px;background:var(--band);text-align:center}
.quote-band p{font-size:11.5px;color:#666;margin-top:8px}
.quote-band strong{display:block;font-size:10.5px;color:var(--brand);letter-spacing:.5px;font-weight:600}
.service{top:386px;width:128px;text-align:center}
.service svg{display:block;margin:0 auto;height:54px}
.service h3{font-size:9.5px;font-weight:600;color:var(--brand);margin-top:17px}
.service p{font-size:7px;line-height:10px;color:var(--muted);margin-top:5px}
.rule{height:1px;background:var(--rule);left:110px;width:548px}
.section-title{left:110px;top:551px;font-size:12.5px;font-weight:600;color:#111}
.card{width:264px;height:107px;background:var(--card);display:flex}
.card .thumb{width:126px;height:107px;flex:none}
.card .body{padding:9px 18px 0 9px}
.card h4{font-size:9px;font-weight:600;color:var(--brand);margin-bottom:5px}
.card p{font-size:7px;line-height:9.8px;color:var(--muted)}
.card b{display:block;font-size:7px;color:#222;margin-top:4px}
.col{top:866px;width:170px}
.col h5{font-size:9.5px;font-weight:600;color:#222;text-transform:uppercase;display:flex;align-items:center;gap:6px}
.col h5:before{content:"";width:9px;height:9px;background:var(--brand)}
.col p{font-size:7px;line-height:11px;color:var(--muted);margin-top:8px}
.col p em{font-style:normal;color:#555}
.col a{color:var(--cyan);text-decoration:none}
.footer{left:0;top:992px;width:767px;height:174px;background:var(--brand)}
.footer-bar{left:0;top:1166px;width:767px;height:34px;background:var(--brand-dark);color:#fff;font-size:7px;text-align:center;line-height:34px}
.f-head{top:1012px;color:#fff;font-size:10.5px;text-transform:uppercase}
.f-head:after{content:"";display:block;width:26px;height:2px;background:var(--cyan);margin-top:5px}
.f-line{top:1035px;height:1px;background:#6d6eb8}
.f-list{top:1055px;color:#fff;font-size:7px;line-height:13.2px;list-style:none}
.input{left:380px;width:120px;height:15px;background:#fff;border-radius:2px;font-size:6.5px;color:#999;padding:2px 8px}
.submit{left:380px;top:1120px;width:40px;height:14px;background:var(--cyan);color:#fff;font-size:6.5px;font-weight:600;display:flex;align-items:center;justify-content:center;border-radius:1px}
.cta{left:524px;width:134px;height:34px;background:var(--red);color:#fff;font-size:12px;display:flex;align-items:center;gap:8px;padding-left:12px}
.phone{left:525px;top:1130px;color:#fff;font-size:11px;font-weight:600}
</style>
</head>
<body>
<header class="abs header"></header>
<div class="abs brand">
  <span class="brand-mark"></span>
  <div><div class="brand-name">KVX</div></div>
  <div class="brand-sub">Kelvaro Print &amp;<br>Reprographics<br>Company, Inc.</div>
</div>
<nav class="abs nav">
  <a class="active">The KVX<br>Difference</a>
  <a>Sustainability</a>
  <a>Products<br>&amp; Services</a>
  <a>Reprographics</a>
  <a>Digital File<br>Management</a>
  <a style="padding-left:10px;padding-right:10px">Color<br>Graphics</a>
  <a>Equipment<br>&amp; Supplies</a>
</nav>

<section class="abs hero" role="img" aria-label="Photo of a printing press roller with colourful printed sheets"></section>
<div class="abs arrow" style="left:0"><svg width="8" height="10"><path d="M6 1 2 5l4 4" stroke="#fff" stroke-width="2" fill="none"/></svg></div>
<div class="abs arrow" style="left:746px"><svg width="8" height="10"><path d="M2 1l4 4-4 4" stroke="#fff" stroke-width="2" fill="none"/></svg></div>
<h1 class="abs hero-title">Lorem Ipsum simplement</h1>
<p class="abs hero-text">Lorem Ipsum est simplement du faux texte employé dans la sition et la misen page avant impression</p>
<div class="abs btn-orange">Read More</div>

<section class="abs quote-band">
  <p>“ Dolore eu feugiat nulla facilisis at vero eros et accumsan et iusto odio dignissim qui blandit ”</p>
  <strong>MARTEN OLSBY</strong>
</section>

<div class="abs service" style="left:109px">
  <svg viewBox="0 0 50 54" width="50"><g fill="none" stroke="var(--brand)" stroke-width="3"><path d="M8 6h10v30l-5 10-5-10z"/><path d="M20 6h10v30l-5 10-5-10z"/><path d="M32 10h10v28l-5 10-5-10z"/></g></svg>
  <h3>Graphic Imaging Services</h3>
  <p>Dolore eu feugiat nulla facilisis at vero eros et accumsan iusto odio dsim qui blandit praesent.</p>
</div>
<div class="abs service" style="left:249px">
  <svg viewBox="0 0 54 54" width="54"><circle cx="27" cy="27" r="24" fill="none" stroke="var(--brand)" stroke-width="4"/><circle cx="27" cy="27" r="15" fill="var(--brand)"/><circle cx="27" cy="27" r="9" fill="#fff"/><circle cx="31" cy="23" r="5" fill="var(--brand)"/></svg>
  <h3>Lastest Digital Technology</h3>
  <p>Dolore eu feugiat nulla facilisis at vero eros et accumsan iusto odio dsim qui blandit praesent.</p>
</div>
<div class="abs service" style="left:389px">
  <svg viewBox="0 0 54 54" width="54"><circle cx="24" cy="30" r="21" fill="var(--brand)"/><g fill="#fff"><circle cx="24" cy="20" r="4.5"/><circle cx="24" cy="40" r="4.5"/><circle cx="14" cy="30" r="4.5"/><circle cx="34" cy="30" r="4.5"/></g><path d="M40 14c4-3 6-7 6-12" stroke="var(--brand)" stroke-width="4" fill="none"/></svg>
  <h3>Digital Film Management</h3>
  <p>Dolore eu feugiat nulla facilisis at vero eros et accumsan iusto odio dsim qui blandit praesent.</p>
</div>
<div class="abs service" style="left:530px">
  <svg viewBox="0 0 54 54" width="54"><rect x="14" y="12" width="26" height="32" fill="none" stroke="var(--brand)" stroke-width="1.5" stroke-dasharray="3 2" transform="rotate(8 27 28)"/><rect x="20" y="22" width="14" height="10" fill="none" stroke="var(--brand)" stroke-width="2"/></svg>
  <h3>Reprographics Service</h3>
  <p>Dolore eu feugiat nulla facilisis at vero eros et accumsan iusto odio dsim qui blandit praesent.</p>
</div>

<div class="abs rule" style="top:529px"></div>
<h2 class="abs section-title">PORTFOLIO</h2>

<article class="abs card" style="left:110px;top:579px">
  <div class="thumb" role="img" aria-label="Photo of rolled blueprints" style="background:linear-gradient(135deg,#dfe8f2,#9fb7cf)"></div>
  <div class="body"><h4>Lorem Ipsum simplement</h4><p>Dolore eu feugiat nulla facilisis at vero eros et accumsan iusto odio dsim qui blandit praesent. Ptatum zzril delenit augue duis dolore te feugait nulla facilisi. Nam liber tempor cum soluta.</p><b>Read More</b></div>
</article>
<article class="abs card" style="left:394px;top:579px">
  <div class="thumb" role="img" aria-label="Photo of a fanned colour swatch guide" style="background:linear-gradient(135deg,#e83a6a,#f5c531 35%,#42b04a 60%,#2b7fd0 85%)"></div>
  <div class="body"><h4>Lorem Ipsum simplement</h4><p>Dolore eu feugiat nulla facilisis at vero eros et accumsan iusto odio dsim qui blandit praesent. Ptatum zzril delenit augue duis dolore te feugait nulla facilisi. Nam liber tempor cum soluta.</p><b>Read More</b></div>
</article>
<article class="abs card" style="left:110px;top:703px">
  <div class="thumb" role="img" aria-label="Photo of patterned printed vinyl samples" style="background:linear-gradient(135deg,#e4477a,#2aa3d8 50%,#c9924a)"></div>
  <div class="body"><h4>Lorem Ipsum simplement</h4><p>Dolore eu feugiat nulla facilisis at vero eros et accumsan iusto odio dsim qui blandit praesent. Ptatum zzril delenit augue duis dolore te feugait nulla facilisi. Nam liber tempor cum soluta.</p><b>Read More</b></div>
</article>
<article class="abs card" style="left:394px;top:703px">
  <div class="thumb" role="img" aria-label="Photo of bound books standing upright" style="background:linear-gradient(135deg,#4a4038,#1c1f2e)"></div>
  <div class="body"><h4>Lorem Ipsum simplement</h4><p>Dolore eu feugiat nulla facilisis at vero eros et accumsan iusto odio dsim qui blandit praesent. Ptatum zzril delenit augue duis dolore te feugait nulla facilisi. Nam liber tempor cum soluta.</p><b>Read More</b></div>
</article>

<div class="abs rule" style="top:837px"></div>

<div class="abs col" style="left:110px">
  <h5>Welcome to KVX</h5>
  <p>Dolore eu feugiat nulla facilisis at vero eros et accumsan et iusto odio dignissim qui blandit prae-sent luptatum zzril delenit augue duis dolore te feugait nulla facilisi. Nam liber tempor cum soluta nobis eleifend option congue nihil imperdiet doming id quod mazim placerat facer possim assum. <a>Read More</a></p>
</div>
<div class="abs col" style="left:302px">
  <h5>Equipment for Sale</h5>
  <p>Dolore eu feugiat nulla facilisis at vero eros et accumsan et iusto odio dignissim qui blandit prae-sent luptatum zzril delenit augue duis dolore te feugait nulla facilisi. Nam liber tempor cum soluta nobis eleifend option congue nihil imperdiet doming id quod mazim placerat facer possim assum. <a>Read More</a></p>
</div>
<div class="abs col" style="left:491px;width:170px">
  <h5>News &amp; Events</h5>
  <p><em>Bobis eleifend option congue nihil imperdiet</em><br>doming id quod mazim placerat facer possim assum. <a>Read More</a></p>
  <p style="margin-top:6px"><em>Nnobis eleifend option congue nihil imperdiet</em><br>doming id quod mazim placerat facer possim assum. <a>Read More</a></p>
</div>

<footer class="abs footer"></footer>
<div class="abs f-line" style="left:110px;width:104px"></div>
<div class="abs f-line" style="left:252px;width:92px"></div>
<div class="abs f-line" style="left:379px;width:122px"></div>
<div class="abs f-line" style="left:524px;width:134px"></div>
<div class="abs f-head" style="left:110px">Latest Posts</div>
<div class="abs f-head" style="left:252px">Site Links</div>
<div class="abs f-head" style="left:379px">Get a Free Qoute</div>
<div class="abs f-head" style="left:537px">We on Maps</div>
<ul class="abs f-list" style="left:111px">
  <li>Lorem ipsum dotslor sicts adfmet</li><li>Nam non disam ersaddos dasssd</li><li>Vestibulum aliquet eros ut ipsum</li><li>Nullam blandit tristique lacuss is</li><li>Ut quis ante dui, eget scelerisque</li><li>Praesent tincidunt duid id sapien</li>
</ul>
<ul class="abs f-list" style="left:253px">
  <li>Home (we start here)</li><li>About (get to know us better)</li><li>Services (all we do)</li><li>Galleries (see our work)</li><li>Blog (the news)</li><li>Contact (get in touch with us)</li>
</ul>
<div class="abs input" style="top:1049px">Name</div>
<div class="abs input" style="top:1068px">Email</div>
<div class="abs input" style="top:1087px;height:27px">Message</div>
<div class="abs submit">Submit</div>
<div class="abs cta" style="top:1051px"><svg width="13" height="14"><rect x="1" y="2" width="11" height="11" fill="none" stroke="#fff" stroke-width="1.5"/><path d="M4 1v3M9 1v3M4 8h5M6.5 5.5v5" stroke="#fff" stroke-width="1.5"/></svg>Order Form</div>
<div class="abs cta" style="top:1091px"><svg width="14" height="14"><circle cx="7" cy="7" r="5.5" fill="none" stroke="#fff" stroke-width="2"/><circle cx="7" cy="7" r="2" fill="#fff"/></svg>Digital Plan-room</div>
<div class="abs phone">Order Now 1-800-555-0142</div>
<div class="abs footer-bar">Copyright 2013 KVX. All Rights Reserved.</div>
</body>
</html>
```